Business Card Design for Occupational Medicine Start Up Company

We need to design a professional business card. We are a healthcare company providing occupational medicine services to blue collar industries. We are professional, efficient and high quality service providers.

Target Market(s)

Blue Collar Industry: Shipbuilding, Ports, Trucking Companies; The Executives and Safety Officers for these companies

Industry/Entity Type

Healthcare

Contact Information for Business Card

Logo, Name, Title, Email, Phone

Other font styles liked:
• Please match our Brand Guide

Requirements
Must have
• Our Company Colors and Logo

```html
<!DOCTYPE html>
<html lang="en">
<head>
<meta charset="utf-8">
<title>Crewline Clinics — Business Card</title>
<link rel="stylesheet" href="https://fonts.googleapis.com/css2?family=Montserrat:wght@400;500;700&display=swap">
<style>
  :root {
    --backdrop: #f4af52;
    --card: #ffffff;
    --navy: #2b3481;
    --sky: #29abe2;
    --amber: #f4af52;
  }
  * { margin: 0; padding: 0; box-sizing: border-box; }
  html, body { width: 1200px; height: 1200px; overflow: hidden; }
  body {
    background: var(--backdrop);
    font-family: "Montserrat", sans-serif;
    position: relative;
  }
  .card {
    position: absolute;
    left: 297px;
    width: 605px;
    height: 345px;
    background: var(--card);
    overflow: hidden;
  }
  .card--front { top: 192px; }
  .card--back { top: 662px; }

  .stripe { position: absolute; left: 0; width: 100%; height: 6px; }
  .stripe--navy { top: 309px; background: var(--navy); }
  .stripe--sky { top: 321px; background: var(--sky); }
  .stripe--amber { top: 333px; background: var(--amber); }

  .vstripe { position: absolute; top: 0; height: 100%; width: 6px; }
  .vstripe--navy { left: 566px; background: var(--navy); }
  .vstripe--sky { left: 578px; background: var(--sky); }
  .vstripe--amber { left: 591px; background: var(--amber); }

  /* front */
  .brand {
    position: absolute;
    top: 108px;
    left: 0;
    width: 100%;
    display: flex;
    flex-direction: column;
    align-items: center;
    gap: 14px;
  }
  .brand__dot {
    width: 60px; height: 60px;
    border-radius: 50%;
    background: var(--navy);
  }
  .brand__name {
    font-weight: 700;
    font-size: 25px;
    color: var(--navy);
    letter-spacing: 0.5px;
  }
  .website {
    position: absolute;
    top: 282px;
    left: 0;
    width: 100%;
    text-align: center;
    font-size: 14px;
    font-weight: 400;
    color: var(--sky);
    letter-spacing: 9px;
    padding-left: 9px;
  }

  /* back */
  .back-brand {
    position: absolute;
    top: 32px;
    left: 19px;
    display: flex;
    align-items: center;
    gap: 10px;
  }
  .back-brand__dot {
    width: 40px; height: 40px;
    border-radius: 50%;
    background: var(--navy);
  }
  .back-brand__name {
    font-weight: 700;
    font-size: 15px;
    color: var(--navy);
  }
  .person {
    position: absolute;
    top: 34px;
    right: 58px;
    text-align: right;
  }
  .person__name {
    font-weight: 700;
    font-size: 24px;
    color: var(--sky);
    letter-spacing: 0.5px;
    line-height: 1.1;
  }
  .person__title {
    margin-top: 6px;
    font-weight: 400;
    font-size: 14px;
    color: var(--navy);
  }
  .contacts {
    position: absolute;
    top: 208px;
    left: 19px;
    list-style: none;
  }
  .contact {
    display: flex;
    align-items: center;
    gap: 12px;
    height: 19px;
    margin-bottom: 13px;
    font-size: 14.5px;
    color: var(--navy);
  }
  .contact__icon {
    width: 19px; height: 19px;
    background: var(--sky);
    display: flex; align-items: center; justify-content: center;
  }
  .contact__icon svg { width: 11px; height: 11px; }
</style>
</head>
<body>

<section class="card card--front">
  <div class="brand">
    <span class="brand__dot"></span>
    <span class="brand__name">CREWLINE CLINICS</span>
  </div>
  <p class="website">crewlinehealth.com</p>
  <span class="stripe stripe--navy"></span>
  <span class="stripe stripe--sky"></span>
  <span class="stripe stripe--amber"></span>
</section>

<section class="card card--back">
  <div class="back-brand">
    <span class="back-brand__dot"></span>
    <span class="back-brand__name">CREWLINE CLINICS</span>
  </div>

  <div class="person">
    <h1 class="person__name">DANIEL R. ASHFORD</h1>
    <p class="person__title">Chief Executive Manager</p>
  </div>

  <ul class="contacts">
    <li class="contact">
      <span class="contact__icon">
        <svg viewBox="0 0 12 12" fill="none" stroke="#fff" stroke-width="1.3">
          <path d="M1.5 6 6 2l4.5 4M3 5v5h6V5M5 10V7.5h2V10"/>
        </svg>
      </span>
      2750 Harbor Lane Portsmouth, VA 23704
    </li>
    <li class="contact">
      <span class="contact__icon">
        <svg viewBox="0 0 12 12" fill="#fff">
          <path d="M2.2 1.2 4 1l1.2 2.6-1.1.9a6 6 0 0 0 3.4 3.4l.9-1.1L11 8l-.2 1.8c-.1.6-.7 1-1.3.9A9 9 0 0 1 1.3 2.5c-.1-.6.3-1.2.9-1.3z"/>
        </svg>
      </span>
      +1 555-014-2290
    </li>
    <li class="contact">
      <span class="contact__icon">
        <svg viewBox="0 0 12 12" fill="none" stroke="#fff" stroke-width="1.2">
          <rect x="1" y="2.5" width="10" height="7"/>
          <path d="M1 2.5 6 7l5-4.5M1 9.5 4.5 6M11 9.5 7.5 6"/>
        </svg>
      </span>
      info@crewlinehealth.com
    </li>
  </ul>

  <span class="stripe stripe--navy"></span>
  <span class="stripe stripe--sky"></span>
  <span class="stripe stripe--amber"></span>
  <span class="vstripe vstripe--navy"></span>
  <span class="vstripe vstripe--sky"></span>
  <span class="vstripe vstripe--amber"></span>
</section>

</body>
</html>
```